4th Generation Family Business Needs a New Card Design!

We are a family owned 4th Generation company. We are based in the Sydney, Australia area and we are desperately in need of a more modern and classy card. We are monumental masons who design, supply & erect lasting memorials throughout cemeteries in Sydney. Our customers are normally in a period of grieving. I have attached logo files that will need to be implemented on the card. Company was established 1935. Australian Owned and Operated. Card needs to be designed to PIXO.com specification.

Target Market(s)

Our target market is based upon people that a grieving for family members that have passed away. We also deal with alot of companies that own and operate cemeteries.

Industry/Entity Type

Business

Contact Information for Business Card

Simon Harcourt, Operations Manager, 0417293086, simon@harcourtmemorials.com.au
Lewis Harcourt, Director, 0491630572, lewis@harcourtmemorials.com.au
Phone # 02 9561 3048
Website: www.harcourtmemorials.com.au
Address: Suite 17, 8 Palfrey Lane, West Carlow, Sydney NSW 2156

Font styles to use
Serif
Decorative
Script

Requirements
Must have
• Would like to see the logo nicely implemented with a modern design. Embossed lettering would be a nice additive.

```html
<!DOCTYPE html>
<html lang="en">
<head>
<meta charset="utf-8">
<title>Harcourt Memorials – Business Card</title>
<link rel="stylesheet" href="https://fonts.googleapis.com/css2?family=Cinzel:wght@400;600&family=Open+Sans:wght@400&display=swap">
<style>
  :root {
    --backdrop: #cfcfcf;
    --card-dark: #0c0c0c;
    --card-mid: #2a2a2a;
    --gold: #f0c12a;
    --silver: #e6e6e6;
    --text-light: #f4f4f4;
  }
  * { box-sizing: border-box; margin: 0; padding: 0; }
  html, body {
    width: 1200px; height: 900px; overflow: hidden;
    background: var(--backdrop);
  }
  .canvas {
    width: 1200px; height: 900px;
    position: relative;
  }
  .card {
    position: absolute;
    left: 290px;
    width: 620px; height: 378px;
    background: radial-gradient(ellipse at 45% 40%, var(--card-mid) 0%, var(--card-dark) 75%);
    box-shadow: 0 10px 24px rgba(0,0,0,0.28);
    color: var(--text-light);
    font-family: "Open Sans", Arial, sans-serif;
  }
  .card--front { top: 52px; }
  .card--back  { top: 470px; }

  /* Front */
  .brand {
    position: absolute; left: 0; right: 0; top: 108px;
    display: flex; flex-direction: column; align-items: center;
  }
  .brand__square {
    width: 18px; height: 18px; background: var(--gold); margin-bottom: 22px;
  }
  .brand__name {
    font-family: "Cinzel", Georgia, serif; font-weight: 600;
    font-size: 38px; letter-spacing: 3px; color: var(--silver);
  }
  .brand__rule {
    width: 300px; height: 2px; background: var(--gold); margin-top: 14px;
  }
  .front-contact {
    position: absolute; left: 0; right: 0; top: 262px;
    text-align: center; font-size: 17px; line-height: 1.45;
  }

  /* Back */
  .people {
    position: absolute; left: 34px; top: 32px;
  }
  .person + .person { margin-top: 20px; }
  .person__name {
    font-family: "Cinzel", Georgia, serif; font-weight: 400;
    color: var(--gold); font-size: 20px; letter-spacing: 0.5px;
  }
  .person__role { font-size: 15px; margin-top: 2px; }
  .person__line {
    display: flex; align-items: center; gap: 8px;
    font-size: 15px; line-height: 1.4;
  }
  .person__line svg { flex: none; }
  .back-brand {
    position: absolute; right: 34px; top: 118px; width: 230px;
    display: flex; align-items: center; gap: 14px;
  }
  .back-brand__square {
    width: 22px; height: 22px; background: var(--gold); flex: none;
  }
  .back-brand__name {
    font-family: "Cinzel", Georgia, serif; font-weight: 600;
    color: var(--gold); font-size: 30px; line-height: 1.1; letter-spacing: 1px;
  }
  .address {
    position: absolute; right: 34px; bottom: 30px;
    text-align: right; font-size: 16px; line-height: 1.35;
  }
</style>
</head>
<body>
<main class="canvas">

  <section class="card card--front" aria-label="Card front">
    <div class="brand">
      <span class="brand__square"></span>
      <span class="brand__name">HARCOURT MEMORIALS</span>
      <span class="brand__rule"></span>
    </div>
    <p class="front-contact">02 9561 3048<br>www.harcourtmemorials.com.au</p>
  </section>

  <section class="card card--back" aria-label="Card back">
    <div class="people">
      <div class="person">
        <p class="person__name">Simon Harcourt</p>
        <p class="person__role">Operations Manager</p>
        <p class="person__line">
          <svg width="10" height="14" viewBox="0 0 10 14"><rect x="1" y="1" width="8" height="12" rx="1.5" fill="none" stroke="#f0c12a" stroke-width="1.6"/><rect x="4" y="10" width="2" height="1.5" fill="#f0c12a"/></svg>
          0417293086
        </p>
        <p class="person__line">
          <svg width="12" height="9" viewBox="0 0 12 9"><rect x="0" y="0" width="12" height="9" fill="#f0c12a"/><path d="M0 0 L6 5 L12 0" fill="none" stroke="#0c0c0c" stroke-width="1.2"/></svg>
          simon@harcourtmemorials.com.au
        </p>
      </div>
      <div class="person">
        <p class="person__name">Lewis Harcourt</p>
        <p class="person__role">Director</p>
        <p class="person__line">
          <svg width="10" height="14" viewBox="0 0 10 14"><rect x="1" y="1" width="8" height="12" rx="1.5" fill="none" stroke="#f0c12a" stroke-width="1.6"/><rect x="4" y="10" width="2" height="1.5" fill="#f0c12a"/></svg>
          0491630572
        </p>
        <p class="person__line">
          <svg width="12" height="9" viewBox="0 0 12 9"><rect x="0" y="0" width="12" height="9" fill="#f0c12a"/><path d="M0 0 L6 5 L12 0" fill="none" stroke="#0c0c0c" stroke-width="1.2"/></svg>
          lewis@harcourtmemorials.com.au
        </p>
      </div>
    </div>

    <div class="back-brand">
      <span class="back-brand__square"></span>
      <span class="back-brand__name">Harcourt Memorials</span>
    </div>

    <p class="address">Suite 17, 8 Palfrey Lane,<br>West Carlow, Sydney NSW 2156</p>
  </section>

</main>
</body>
</html>
```